Veldmark Supplies Business Card

Professional business card that stand out to our potential customers. Front and back with clean modern design

Industry/Entity Type

Oil and gas

Contact Information for Business Card

Name, address, website , office phone and cell number

Requirements
Must have
• Editable files for each employee

```html
<!DOCTYPE html>
<html lang="en">
<head>
<meta charset="utf-8">
<title>Veldmark Supplies Business Card</title>
<link rel="stylesheet" href="https://fonts.googleapis.com/css2?family=Roboto:wght@400;500&display=swap">
<style>
  :root {
    --backdrop: #2b2b2b;
    --card: #1f1f20;
    --card-edge: #2a2a2b;
    --red: #e32b36;
    --cyan: #2db3d6;
    --text: #dcdcdc;
    --muted: #b9b9b9;
  }
  * { box-sizing: border-box; margin: 0; padding: 0; }
  html, body { width: 1200px; height: 852px; overflow: hidden; }
  body {
    background: var(--backdrop);
    font-family: "Roboto", Arial, sans-serif;
    display: flex;
    align-items: center;
    justify-content: center;
    gap: 60px;
  }
  .card {
    position: relative;
    width: 500px;
    height: 290px;
    background: var(--card);
    border: 1px solid var(--card-edge);
    border-radius: 22px;
    box-shadow: 0 18px 40px rgba(0,0,0,.45);
    overflow: hidden;
  }
  .card-front .brand-name {
    position: absolute;
    left: 48px;
    top: 122px;
    display: flex;
    align-items: center;
    gap: 14px;
  }
  .brand-square {
    width: 34px;
    height: 34px;
    background: var(--red);
  }
  .brand-text {
    font-weight: 500;
    font-size: 30px;
    letter-spacing: .5px;
    color: var(--red);
    text-transform: uppercase;
  }
  .card-back .brand-name {
    position: absolute;
    left: 36px;
    top: 34px;
    display: flex;
    align-items: center;
    gap: 10px;
  }
  .card-back .brand-square { width: 24px; height: 24px; }
  .card-back .brand-text { font-size: 19px; }
  .contact {
    position: absolute;
    left: 36px;
    top: 98px;
    color: var(--text);
  }
  .person-name {
    font-size: 22px;
    font-weight: 500;
    color: var(--cyan);
  }
  .person-title {
    font-size: 14px;
    color: var(--muted);
    margin-top: 2px;
  }
  .address {
    font-size: 14px;
    line-height: 1.4;
    margin-top: 12px;
    font-style: normal;
  }
  .contact-list {
    list-style: none;
    margin-top: 10px;
    font-size: 14px;
    line-height: 1.55;
  }
  .contact-list li { display: flex; align-items: center; gap: 8px; }
  .contact-list svg { width: 13px; height: 13px; fill: var(--red); flex: none; }
</style>
</head>
<body>
  <section class="card card-front" aria-label="Card front">
    <div class="brand-name">
      <span class="brand-square"></span>
      <span class="brand-text">Veldmark Supplies</span>
    </div>
  </section>

  <section class="card card-back" aria-label="Card back">
    <div class="brand-name">
      <span class="brand-square"></span>
      <span class="brand-text">Veldmark Supplies</span>
    </div>
    <div class="contact">
      <p class="person-name">Jordan Reyes</p>
      <p class="person-title">Managing Director</p>
      <address class="address">412 Harlan Ridge Suite 3<br>Midvale, Tx 79012</address>
      <ul class="contact-list">
        <li>
          <svg viewBox="0 0 16 16" aria-hidden="true"><path d="M3.5 1h2.5l1.3 3.3-1.6 1.1a8 8 0 0 0 4.9 4.9l1.1-1.6L15 10v2.5A2 2 0 0 1 13 14.5 12.5 12.5 0 0 1 1.5 3 2 2 0 0 1 3.5 1z"/></svg>
          (555)014-0288
        </li>
        <li>
          <svg viewBox="0 0 16 16" aria-hidden="true"><path d="M1 3h14v10H1z M1.8 3.8 8 9l6.2-5.2" stroke="#1f1f20" stroke-width="1.2"/></svg>
          sales@veldmarksupplies.com
        </li>
        <li>
          <svg viewBox="0 0 16 16" aria-hidden="true"><circle cx="8" cy="8" r="7"/><path d="M1 8h14M8 1c-3 3.5-3 10.5 0 14M8 1c3 3.5 3 10.5 0 14" stroke="#1f1f20" stroke-width="1" fill="none"/></svg>
          www.veldmarksupplies.com
        </li>
      </ul>
    </div>
  </section>
</body>
</html>
```